Brightwave Reach - Business Card

We need a business card for a Social Media Marketing company that specializes in online marketing for small businesses in Canada using common Social Media platforms such as Pixlora, Chatterly, Blinkpost & Quibber.

I have uploaded a copy of our logo which I would like utilized in the business card. We would like the business card to be modern yet classy design.

Our website is www.brightwavereach.ca

Industry/Entity Type

Marketing

Contact Information for Business Card

Email: info@brightwavereach.ca
Website: www.brightwavereach.ca
Telephone: 604-555-0193

Colors

Designer to choose colors to be used in the design.

Requirements
Must have
• Social Media icons on reverse
• Please add some designs with color.

```html
<!DOCTYPE html>
<html lang="en">
<head>
<meta charset="utf-8">
<title>Brightwave Reach – Business Card</title>
<link href="https://fonts.googleapis.com/css2?family=Roboto:wght@400;700&family=Roboto+Condensed:wght@700&display=swap" rel="stylesheet">
<style>
  :root {
    --backdrop: #3a3f42;
    --card-white: #ffffff;
    --card-dark: #474d50;
    --card-dark-deep: #3f4447;
    --accent-red: #e8332d;
    --ink: #3d4245;
    --ink-soft: #5a5f62;
  }
  * { box-sizing: border-box; margin: 0; padding: 0; }
  html, body { width: 1200px; height: 1000px; overflow: hidden; }
  body { background: var(--backdrop); font-family: "Roboto", Arial, sans-serif; position: relative; }

  .card { position: absolute; width: 540px; height: 310px; box-shadow: 0 14px 30px rgba(0,0,0,.35); overflow: hidden; }

  /* front */
  .card-front { left: 60px; top: 170px; background: var(--card-white); }
  .accent-bar { position: absolute; left: 70px; width: 170px; height: 16px; background: var(--accent-red); }
  .accent-bar.top { top: 0; }
  .accent-bar.bottom { bottom: 0; }

  .wordmark { position: absolute; display: flex; align-items: center; gap: 10px;
    font-family: "Roboto Condensed", "Arial Narrow", sans-serif; font-weight: 700; text-transform: uppercase; line-height: .95; }
  .wordmark .mark-square { width: 16px; height: 16px; border: 2px solid currentColor; flex: none; }
  .card-front .wordmark { left: 60px; top: 118px; color: var(--ink); font-size: 30px; }

  .contact { position: absolute; left: 300px; top: 112px; color: var(--ink); }
  .contact .person { color: var(--accent-red); font-weight: 700; font-size: 17px; letter-spacing: .3px; text-transform: uppercase; }
  .contact .role { font-size: 13px; color: var(--ink-soft); margin-bottom: 14px; }
  .contact ul { list-style: none; }
  .contact li { display: flex; align-items: center; gap: 9px; font-size: 12.5px; margin-bottom: 5px; }
  .contact svg { width: 12px; height: 12px; fill: var(--ink); flex: none; }

  /* back */
  .card-back { left: 600px; top: 520px; background: linear-gradient(160deg, var(--card-dark) 0%, var(--card-dark-deep) 100%); }
  .card-back .wordmark { left: 0; right: 0; top: 92px; justify-content: center; color: var(--card-white); font-size: 34px; }
  .social-band { position: absolute; left: 0; bottom: 0; width: 540px; height: 110px; }
  .social-row { position: absolute; left: 60px; right: 60px; top: 212px; display: flex; justify-content: space-between; }
  .social-item { display: flex; flex-direction: column; align-items: center; gap: 6px; width: 90px; }
  .social-dot { width: 34px; height: 34px; border-radius: 50%; background: var(--accent-red); border: 3px solid var(--card-white); box-shadow: 0 1px 3px rgba(0,0,0,.3); }
  .social-name { font-size: 12px; font-weight: 700; color: var(--ink); }
</style>
</head>
<body>

<section class="card card-front" aria-label="Business card front">
  <div class="accent-bar top"></div>
  <div class="accent-bar bottom"></div>
  <div class="wordmark"><span class="mark-square"></span><span>Brightwave<br>Reach</span></div>
  <div class="contact">
    <p class="person">Daniel Carver</p>
    <p class="role">Manager</p>
    <ul>
      <li><svg viewBox="0 0 24 24"><path d="M6.6 10.8a15 15 0 0 0 6.6 6.6l2.2-2.2c.3-.3.7-.4 1-.2 1.1.4 2.3.6 3.6.6.6 0 1 .4 1 1V20c0 .6-.4 1-1 1A17 17 0 0 1 3 4c0-.6.4-1 1-1h3.5c.6 0 1 .4 1 1 0 1.3.2 2.5.6 3.6.1.3 0 .7-.2 1z"/></svg>604-555-0193</li>
      <li><svg viewBox="0 0 24 24"><path d="M2 5h20v14H2zm2 2v.5l8 5 8-5V7l-8 5z"/></svg>info@brightwavereach.ca</li>
      <li><svg viewBox="0 0 24 24"><path d="M12 2a10 10 0 1 0 0 20 10 10 0 0 0 0-20zm6.9 6h-3a15 15 0 0 0-1.3-3.9A8 8 0 0 1 18.9 8zM12 4c.8 1.2 1.5 2.5 1.9 4h-3.8c.4-1.5 1.1-2.8 1.9-4zM4.3 14a8 8 0 0 1 0-4h3.4a16 16 0 0 0 0 4zm.8 2h3a15 15 0 0 0 1.3 3.9A8 8 0 0 1 5.1 16zm3-8h-3a8 8 0 0 1 4.3-3.9C8.8 5.3 8.4 6.6 8.1 8zM12 20c-.8-1.2-1.5-2.5-1.9-4h3.8c-.4 1.5-1.1 2.8-1.9 4zm2.3-6H9.7a14 14 0 0 1 0-4h4.6a14 14 0 0 1 0 4zm.3 5.9c.6-1.2 1-2.5 1.3-3.9h3a8 8 0 0 1-4.3 3.9zm1.7-5.9a16 16 0 0 0 0-4h3.4a8 8 0 0 1 0 4z"/></svg>www.brightwavereach.ca</li>
    </ul>
  </div>
</section>

<section class="card card-back" aria-label="Business card back">
  <div class="wordmark"><span class="mark-square"></span><span>Brightwave<br>Reach</span></div>
  <svg class="social-band" viewBox="0 0 540 110" aria-hidden="true">
    <path d="M0 40 H40 Q50 30 62 30 H470 Q482 30 488 40 V70 Q492 80 505 80 H540 V110 H0 Z" fill="#ffffff"/>
  </svg>
  <div class="social-row">
    <div class="social-item"><span class="social-dot"></span><span class="social-name">Quibber</span></div>
    <div class="social-item"><span class="social-dot"></span><span class="social-name">Blinkpost</span></div>
    <div class="social-item"><span class="social-dot"></span><span class="social-name">Pixlora</span></div>
    <div class="social-item"><span class="social-dot"></span><span class="social-name">Chatterly</span></div>
  </div>
</section>

</body>
</html>
```